New Business Card Design Project

Use the flyer uploaded and website www.brightoakbuilders.com for inspiration.
List Our Services on Backside of business cards
Marcus Delling
Harborline Builders Inc.
Licensed General Contractors
858-471-6093

Contact Information for Business Card

Use the flyer uploaded and website www.brightoakbuilders.com for inspiration. List Our Services on Backside of business cards Marcus Delling Harborline Builders Inc. Licensed General Contractors 858-471-6093

```html
<!DOCTYPE html>
<html lang="en">
<head>
<meta charset="utf-8">
<title>Harborline Builders – Business Cards</title>
<link rel="stylesheet" href="https://fonts.googleapis.com/css2?family=Marcellus&family=Montserrat:wght@500;600;800&display=swap">
<style>
  :root {
    --bg: #2a2a2a;
    --card-blue: #3580c6;
    --disc-black: #121212;
    --accent-red: #ec1c24;
    --ink-white: #ffffff;
  }
  * { margin: 0; padding: 0; box-sizing: border-box; }
  html, body { width: 1200px; height: 1015px; overflow: hidden; }
  body {
    background: var(--bg);
    font-family: "Montserrat", sans-serif;
    color: var(--ink-white);
  }
  .sheet {
    position: relative;
    width: 1200px;
    height: 1015px;
    display: flex;
    flex-direction: column;
    align-items: center;
    justify-content: center;
    gap: 31px;
  }
  .card {
    position: relative;
    width: 800px;
    height: 457px;
    background: var(--card-blue);
    overflow: hidden;
    box-shadow: 0 10px 28px rgba(0,0,0,0.55);
  }
  .card__disc { position: absolute; inset: 0; width: 800px; height: 457px; }
  .brand {
    position: absolute;
    left: 490px;
    top: 200px;
    width: 300px;
    text-align: center;
    white-space: nowrap;
    font-family: "Marcellus", serif;
    font-size: 20px;
    letter-spacing: 1.5px;
    line-height: 1.2;
    color: var(--ink-white);
  }
  .rule {
    display: block;
    width: 56px;
    height: 1px;
    background: var(--ink-white);
  }

  /* Services side */
  .services { position: absolute; left: 56px; top: 62px; }
  .services__title {
    font-weight: 800;
    font-size: 26px;
    letter-spacing: 0.5px;
  }
  .services .rule { margin: 10px 0 18px 14px; }
  .services__list { list-style: none; padding-left: 28px; }
  .services__list li {
    font-weight: 500;
    font-size: 17px;
    line-height: 27px;
    white-space: nowrap;
  }

  /* Contact side */
  .contact { position: absolute; left: 50px; top: 92px; }
  .contact__name {
    font-family: "Marcellus", serif;
    font-weight: 400;
    font-size: 28px;
    letter-spacing: 1px;
    white-space: nowrap;
  }
  .contact .rule { margin: 12px 0 24px 12px; }
  .contact__list { list-style: none; padding-left: 30px; }
  .contact__list li {
    display: flex;
    align-items: center;
    gap: 10px;
    font-weight: 500;
    font-size: 16px;
    line-height: 30px;
    white-space: nowrap;
  }
  .contact__list svg { width: 18px; height: 18px; flex: none; }
  .contact .rule--lower { margin: 24px 0 20px 44px; }
  .contact__company {
    padding-left: 60px;
    font-weight: 600;
    font-size: 17px;
    line-height: 26px;
    white-space: nowrap;
  }
</style>
</head>
<body>
<main class="sheet">

  <section class="card card--services" aria-label="Business card, services side">
    <svg class="card__disc" viewBox="0 0 800 457" aria-hidden="true">
      <circle cx="643" cy="152" r="262" fill="var(--disc-black)"/>
      <circle cx="651" cy="148" r="252" fill="var(--accent-red)"/>
      <circle cx="665" cy="142" r="242" fill="var(--disc-black)"/>
    </svg>
    <p class="brand">HARBORLINE BUILDERS</p>
    <div class="services">
      <h2 class="services__title">OUR SERVICES</h2>
      <span class="rule"></span>
      <ul class="services__list">
        <li>Remodel: Kitchen &amp; Bath</li>
        <li>Painting: Interior &amp; Exterior</li>
        <li>Flooring: Carpet, Vinyl, Wood</li>
        <li>Window &amp; Door Replacement</li>
        <li>Plumbing: Repairs &amp; Upgrades</li>
        <li>Energy-Efficient Upgrades</li>
        <li>Deck &amp; Patio Construction</li>
        <li>Water &amp; Mold Damage</li>
        <li>Garage Renovation</li>
      </ul>
    </div>
  </section>

  <section class="card card--contact" aria-label="Business card, contact side">
    <svg class="card__disc" viewBox="0 0 800 457" aria-hidden="true">
      <circle cx="643" cy="152" r="262" fill="var(--disc-black)"/>
      <circle cx="651" cy="148" r="252" fill="var(--accent-red)"/>
      <circle cx="665" cy="142" r="242" fill="var(--disc-black)"/>
    </svg>
    <p class="brand">HARBORLINE BUILDERS</p>
    <div class="contact">
      <h1 class="contact__name">MARCUS DELLING</h1>
      <span class="rule"></span>
      <ul class="contact__list">
        <li>
          <svg viewBox="0 0 24 24" aria-hidden="true"><path fill="var(--ink-white)" d="M6.6 10.8a15.1 15.1 0 0 0 6.6 6.6l2.2-2.2c.3-.3.7-.4 1-.2 1.1.4 2.3.6 3.6.6.6 0 1 .4 1 1V20c0 .6-.4 1-1 1A17 17 0 0 1 3 4c0-.6.4-1 1-1h3.5c.6 0 1 .4 1 1 0 1.3.2 2.5.6 3.6.1.3 0 .7-.2 1z"/></svg>
          858-471-6093
        </li>
        <li>
          <svg viewBox="0 0 24 24" aria-hidden="true"><path fill="var(--ink-white)" d="M2 5h20v14H2zm2 2v.5l8 5 8-5V7zm0 2.8V17h16V9.8l-8 5z"/></svg>
          info@brightoakbuilders.com
        </li>
        <li>
          <svg viewBox="0 0 24 24" aria-hidden="true" fill="none" stroke="var(--ink-white)" stroke-width="1.8"><circle cx="12" cy="12" r="9"/><ellipse cx="12" cy="12" rx="4" ry="9"/><path d="M3 12h18M4.5 7.5h15M4.5 16.5h15"/></svg>
          www.brightoakbuilders.com
        </li>
      </ul>
      <span class="rule rule--lower"></span>
      <p class="contact__company">Harborline Builders Inc.<br>Licensed General Contractors</p>
    </div>
  </section>

</main>
</body>
</html>
```